Website for IT consulting Company

I need a website upgrade, the existing site content is ok, I would also like to add a testimonial page, the site should be something that is easy for us to update content. You use the content from www.kelvanbrook.com as an example. I will also post update logo and artwork. I also need a contact form with some type of validation or captcha.

I added Coded to the Project

Please omit Address maps

Target Market(s)

small business, service oriented companies. We provide IT Consulting, support and mangement

Industry/Entity Type

Information Technology

Coding

Number of Pages Required

1 page

Font styles to use
Serif
Sans Serif

Requirements
Must have
• Contain logo attached, and content from existing web site www.kelvanbrook.com.
• Also need to update content easily, and be movable to different platforms.
• There is a catch phrase
• "Let us worry about your technology…” “ so you don’t have to!”
• Should be included.
Nice to have
• Testimonial page, Project page where we can post new and past projects and pictures
Should not have
• none

```html
<!DOCTYPE html>
<html lang="en">
<head>
<meta charset="utf-8">
<title>Kelvanbrook Technology Group — IT solutions that work for your business</title>
<link rel="stylesheet" href="https://fonts.googleapis.com/css2?family=Roboto:ital,wght@0,300;0,400;0,500;0,700;1,400&display=swap">
<style>
:root{
  --blue:#3a9ad9;
  --blue-deep:#2a7cc7;
  --blue-dark:#1f6fb8;
  --blue-text:#2488d4;
  --ink:#222;
  --muted:#8a8a8a;
  --body:#555;
  --pale:#f4f4f4;
  --white:#fff;
  --rule:#7fb8e2;
}
*{margin:0;padding:0;box-sizing:border-box}
html,body{width:1200px;height:2473px;overflow:hidden}
body{font-family:"Roboto",Arial,sans-serif;color:var(--ink);background:var(--white);position:relative}
.section-title{font-size:23px;font-weight:500;text-align:center;color:var(--ink)}
.section-title span{color:var(--blue-text)}
.dotted-rule{border:0;border-top:1px dashed var(--rule);margin:0 51px}

/* hero */
.hero{position:absolute;left:0;top:0;width:1200px;height:544px;
  background:linear-gradient(160deg,#5aa8e2 0%,#3f8fd3 45%,#2e78bf 100%)}
.hero-photo{position:absolute;inset:0;background:
  radial-gradient(ellipse at 75% 35%,rgba(255,255,255,.18),transparent 55%),
  radial-gradient(ellipse at 20% 70%,rgba(20,70,140,.25),transparent 60%)}
.nav{position:absolute;top:0;left:0;width:1200px;height:66px;border-bottom:1px solid rgba(255,255,255,.25)}
.brand{position:absolute;left:48px;top:10px;color:var(--white)}
.brand-name{display:flex;align-items:center;gap:8px;font-size:24px;font-weight:700;letter-spacing:.5px}
.brand-mark{width:22px;height:22px;background:var(--white);border-radius:3px}
.brand-tag{font-size:8px;font-weight:300;margin-top:3px;margin-left:30px;opacity:.9}
.nav-links{position:absolute;left:366px;top:24px;display:flex}
.nav-links a{color:var(--white);text-decoration:none;font-size:16px;display:inline-block;white-space:nowrap}
.nav-about{width:87px}
.nav-support{width:107px}
.nav-clients{width:101px}
.nav-project{width:105px}
.nav-actions{position:absolute;right:44px;top:16px;display:flex;gap:7px}
.btn-pill{height:32px;border-radius:16px;font-size:13px;font-weight:500;display:flex;align-items:center;justify-content:center}
.btn-login{width:62px;border:2px solid var(--white);color:var(--white)}
.btn-contact{width:90px;background:var(--white);color:var(--ink)}
.hero-copy{position:absolute;top:225px;width:1200px;text-align:center;color:var(--white)}
.hero-copy h1{font-size:28px;font-weight:500}
.hero-copy p{font-size:27px;font-weight:300;margin-top:16px}
.btn-more{display:inline-block;margin-top:22px;width:106px;height:33px;line-height:30px;border:2px solid var(--white);border-radius:5px;font-size:12px;font-weight:500}

/* welcome */
.welcome{position:absolute;top:544px;left:0;width:1200px;height:132px;background:var(--blue);color:var(--white);text-align:center}
.welcome h2{font-size:22px;font-weight:500;padding-top:5px}
.welcome hr{border:0;border-top:1px dashed rgba(255,255,255,.8);margin:10px 51px 12px}
.welcome p{font-size:12.5px;line-height:20px;padding:0 50px}

/* services */
.services{position:absolute;top:676px;left:0;width:1200px;height:586px;background:var(--pale)}
.services .section-title{padding-top:8px}
.services .dotted-rule{margin-top:9px;border-top-color:#888}
.service-card{position:absolute;width:348px;height:174px}
.service-photo{position:absolute;left:0;top:0;width:348px;height:154px;border-radius:3px}
.service-label{position:absolute;left:14px;top:132px;width:320px;height:42px;background:var(--blue);color:var(--white);font-size:14px;line-height:42px;text-align:center;border-radius:2px}
.service-icon{position:absolute;left:151px;top:-24px;width:46px;height:46px;border-radius:50%;background:var(--blue-deep);border:3px solid var(--white);display:flex;align-items:center;justify-content:center}

/* feature columns */
.features{position:absolute;top:1262px;left:0;width:1200px;height:233px;display:flex}
.feature{color:var(--white);text-align:center;padding:22px 24px 0}
.feature h3{font-size:28px;font-weight:500;line-height:29px}
.feature p{font-size:15px;line-height:23px;margin:20px 28px 0}
.feature-a{width:400px;background:var(--blue)}
.feature-b{width:401px;background:var(--blue-dark)}
.feature-b h3{margin-bottom:14px}
.feature-b p{margin:0 34px}
.feature-c{width:399px;background:var(--blue)}

/* projects */
.projects{position:absolute;top:1495px;left:0;width:1200px;height:395px}
.projects .section-title{padding-top:8px}
.projects .dotted-rule{margin-top:10px}
.project{position:absolute;top:76px;width:254px;text-align:center}
.project-photo{width:254px;height:206px}
.project h4{font-size:18px;font-weight:500;margin-top:28px}
.project p{font-size:13px;line-height:20px;color:var(--muted);margin-top:12px}

/* testimonials */
.testimonials{position:absolute;top:1890px;left:0;width:1200px;height:351px;background:var(--pale)}
.testimonials .section-title{padding-top:12px}
.testimonials .dotted-rule{margin-top:10px}
.quote{position:absolute;font-size:13px;line-height:20px}
.quote blockquote{font-style:italic;color:var(--body)}
.quote cite{display:block;font-style:normal;color:var(--ink);margin-top:7px}
.quote-left{left:56px;width:406px;text-align:right;padding-right:4px}
.quote-right{left:738px;width:412px}
.avatar{position:absolute;width:76px;height:76px;border-radius:50%;background:radial-gradient(circle at 50% 40%,#d9cfc6,#a8a09a)}
.split-v{position:absolute;left:600px;top:94px;height:230px;border-left:1px dashed var(--rule)}
.split-h{position:absolute;left:51px;top:208px;width:1098px;border-top:1px dashed var(--rule)}

/* like strip */
.likes{position:absolute;top:2241px;left:0;width:1200px;height:75px}
.likes-rule{position:absolute;left:66px;top:35px;width:1068px;border-top:1px solid #ddd}
.likes-pill{position:absolute;left:376px;top:13px;width:448px;height:45px;border:1px solid #ddd;border-radius:23px;background:var(--white)}
.likes-thumb{position:absolute;left:20px;top:12px}
.likes-btn{position:absolute;left:120px;top:13px;width:45px;height:19px;background:var(--blue-deep);color:var(--white);font-size:11px;font-weight:700;line-height:19px;text-align:center;border-radius:2px}
.likes-count{position:absolute;left:172px;top:14px;font-size:11px;color:#333}

/* footer */
.footer{position:absolute;top:2316px;left:0;width:1200px;height:157px;border-top:5px solid var(--blue-deep)}
.footer-nav{position:absolute;left:62px;top:52px;display:flex;align-items:center;gap:24px;font-size:13px;font-weight:500}
.footer-rule{position:absolute;left:62px;top:80px;width:1080px;border-top:1px solid #e2e2e2}
.footer-links{position:absolute;left:62px;top:95px;display:flex;gap:17px;font-size:11px;color:#333}
.footer-social{position:absolute;left:568px;top:93px;display:flex;gap:7px}
.footer-social span{width:17px;height:17px;background:var(--blue-deep);border-radius:2px}
.footer-legal{position:absolute;right:56px;top:95px;display:flex;gap:22px;font-size:11px;color:#333}
.footer-brand{position:absolute;right:56px;top:22px;color:var(--blue-deep)}
.footer-brand .brand-name{font-size:20px}
.footer-brand .brand-mark{background:var(--blue-deep);width:18px;height:18px}
.footer-brand .brand-tag{color:#666;margin-left:26px}
.footer-base{position:absolute;left:0;bottom:0;width:1200px;height:5px;background:var(--blue-deep)}
</style>
</head>
<body>

<header class="hero">
  <div class="hero-photo" role="img" aria-label="Blue-tinted photo of a person working at a laptop with a line chart overlay"></div>
  <nav class="nav">
    <div class="brand">
      <div class="brand-name"><span class="brand-mark"></span>KELVANBROOK</div>
      <div class="brand-tag">Let us worry about your technology… so you don't have to!</div>
    </div>
    <div class="nav-links">
      <a class="nav-about" href="#">ABOUT</a><a class="nav-support" href="#">SUPPORT</a><a class="nav-clients" href="#">CLIENTS</a><a class="nav-project" href="#">PROJECT</a><a href="#">CAREERS</a>
    </div>
    <div class="nav-actions">
      <span class="btn-pill btn-login">Log In</span>
      <span class="btn-pill btn-contact">Contact Us</span>
    </div>
  </nav>
  <div class="hero-copy">
    <h1>IT solutions that work for your business.</h1>
    <p>A full service technology company.</p>
    <span class="btn-more">Learn More</span>
  </div>
</header>

<section class="welcome">
  <h2>Welcome to Kelvanbrook Technology Group, Inc</h2>
  <hr>
  <p>Outsourcing is subcontracting a process, such as product design or manufacturing, to a third-party company.[1] The decision to outsource is often made in the interest of lowering firm costs, redirecting or conserving energy directed at the competencies of a particular business, or to make more efficient use of land, labor, capital, (information) technology and resources. Outsourcing became part of the business lexicon during the 1980s</p>
</section>

<section class="services">
  <h2 class="section-title">IT Support <span>Solutions</span></h2>
  <hr class="dotted-rule">

  <div class="service-card" style="left:51px;top:109px">
    <div class="service-photo" role="img" aria-label="Technicians working at a server rack" style="background:linear-gradient(120deg,#3b4a5e,#8a95a3 55%,#d8dde2)"></div>
    <div class="service-icon"><svg width="20" height="20" viewBox="0 0 20 20"><rect x="3" y="3" width="14" height="10" fill="none" stroke="#fff" stroke-width="2"/><rect x="7" y="15" width="6" height="2" fill="#fff"/></svg></div>
    <div class="service-label">Network Administration</div>
  </div>
  <div class="service-card" style="left:425px;top:109px">
    <div class="service-photo" role="img" aria-label="Bundles of blue network cables" style="background:linear-gradient(120deg,#1d4fa0,#3f7fd6 50%,#1a3f86)"></div>
    <div class="service-icon" style="background:#2c3e66"><svg width="20" height="20" viewBox="0 0 20 20"><path d="M10 2 17 6v8l-7 4-7-4V6z" fill="none" stroke="#fff" stroke-width="1.6"/></svg></div>
    <div class="service-label">Network Cabling</div>
  </div>
  <div class="service-card" style="left:796px;top:109px">
    <div class="service-photo" role="img" aria-label="Group of business people in suits" style="background:linear-gradient(90deg,#e9eaec,#7b7f86 40%,#3a3e47 70%,#e2e4e7)"></div>
    <div class="service-icon"><svg width="20" height="20" viewBox="0 0 20 20"><rect x="4" y="9" width="12" height="9" rx="1" fill="#fff"/><path d="M6.5 9V6a3.5 3.5 0 0 1 7 0v3" fill="none" stroke="#fff" stroke-width="2"/></svg></div>
    <div class="service-label">Network Security</div>
  </div>

  <div class="service-card" style="left:51px;top:380px">
    <div class="service-photo" role="img" aria-label="Two colleagues working at a laptop" style="background:linear-gradient(100deg,#d7dde2,#8d8a86 45%,#4a4a4c 80%)"></div>
    <div class="service-icon"><svg width="20" height="20" viewBox="0 0 20 20"><rect x="2" y="4" width="12" height="9" fill="#fff"/><rect x="15" y="4" width="3" height="12" fill="#fff"/></svg></div>
    <div class="service-label">Desktop Support</div>
  </div>
  <div class="service-card" style="left:425px;top:380px">
    <div class="service-photo" role="img" aria-label="Hands using a tablet beside a laptop" style="background:linear-gradient(120deg,#c9c9c9,#ededed 45%,#9a9a9a)"></div>
    <div class="service-icon"><svg width="20" height="20" viewBox="0 0 20 20"><rect x="5" y="2" width="10" height="16" rx="2" fill="none" stroke="#fff" stroke-width="2"/><circle cx="10" cy="15" r="1" fill="#fff"/></svg></div>
    <div class="service-label">Wireless Networks</div>
  </div>
  <div class="service-card" style="left:796px;top:380px">
    <div class="service-photo" role="img" aria-label="Businessman in glasses and a navy suit" style="background:linear-gradient(90deg,#fafafa 30%,#c7b9ad 60%,#2a3550)"></div>
    <div class="service-icon"><svg width="20" height="20" viewBox="0 0 20 20"><rect x="2" y="5" width="16" height="11" fill="#fff"/><path d="M2 5l8 6 8-6" fill="none" stroke="#2a7cc7" stroke-width="1.5"/></svg></div>
    <div class="service-label">Antivirus Solutions</div>
  </div>
</section>

<section class="features">
  <div class="feature feature-a">
    <h3>IT Infrastructure Design and Installation</h3>
    <p>Our staff will design, service, administer and maintain your IT needs.<br>We are well versed on all major operating system, and network<br>appliances</p>
  </div>
  <div class="feature feature-b">
    <h3>Managed IT Solutions</h3>
    <p>Do you need a quick solution to a technical problem? With our live remote-assistance tool, a member of our support team can view your desktop and share control of your mouse and keyboard to get you on your way to a solution.</p>
  </div>
  <div class="feature feature-c">
    <h3>Remote Diagnostic and Support</h3>
    <p>Do you have more than one site? Do you need remote access? We can design and implement LANS/WANS and VPN's. Make your important data available to you wherever you are.</p>
  </div>
</section>

<section class="projects">
  <h2 class="section-title">Latest <span>Project</span></h2>
  <hr class="dotted-rule">
  <div class="project" style="left:51px">
    <div class="project-photo" role="img" aria-label="Cheerful woman with raised arms at a laptop" style="background:linear-gradient(120deg,#e3e6ea,#b9c4d2 55%,#eef0f2)"></div>
    <h4>Ultra Responsive</h4>
    <p>Lorem ipsum dolor sit amet einem,<br>consectetur adipiscing elit, sed do in.</p>
  </div>
  <div class="project" style="left:333px">
    <div class="project-photo" role="img" aria-label="Hands with a pen over printed charts" style="background:linear-gradient(130deg,#f1f1f1,#d8d8d8 50%,#f7f7f7)"></div>
    <h4>Unique Features</h4>
    <p>Eiusmod tempor incididunt ut labore et<br>dolore magna aliqua ut enim ad.</p>
  </div>
  <div class="project" style="left:613px">
    <div class="project-photo" role="img" aria-label="Smiling man on the phone at a laptop" style="background:linear-gradient(100deg,#f2f2f2,#c7c9cc 45%,#2d3a52 80%)"></div>
    <h4>Easy to Customize</h4>
    <p>Aliquip ex ea commodo consequat. Duis<br>aute irure dolor in reprehenderit.</p>
  </div>
  <div class="project" style="left:895px">
    <div class="project-photo" role="img" aria-label="Tablet showing a dashboard on a desk" style="background:linear-gradient(130deg,#f5f5f5,#c9ced6 50%,#eef0f3)"></div>
    <h4>Layout Builder</h4>
    <p>Duis aute irure dolor in reprehenderit in<br>voluptate velit esse cillum dolore.</p>
  </div>
</section>

<section class="testimonials">
  <h2 class="section-title">What <span>People Say</span></h2>
  <hr class="dotted-rule">
  <div class="split-v"></div>
  <div class="split-h"></div>

  <div class="quote quote-left" style="top:98px">
    <blockquote>Duis aute irure dolor in reprehenderit in voluptate velit esse cillum dolore eu fugiat nulla pariatur. Excepteur sint occaecat cupidatat non proident, sunt in culpa qui officia deserunt mollit.</blockquote>
    <cite>Mark Ellison, Operations Manager</cite>
  </div>
  <div class="avatar" style="left:491px;top:101px" role="img" aria-label="Portrait photo of the reviewer"></div>

  <div class="avatar" style="left:634px;top:101px" role="img" aria-label="Portrait photo of the reviewer"></div>
  <div class="quote quote-right" style="top:98px">
    <blockquote>Provident, similique sunt in culpa qui officia deserunt mollitia animi, id est laborum et dolorum fuga. Et harum quidem rerum facilis est et expedita distinctio. Nam libero tempore, cum soluta nobis.</blockquote>
    <cite>Nora Whitfield, Creative Designer</cite>
  </div>

  <div class="quote quote-left" style="top:236px">
    <blockquote>Luis aute irure dolor in piluptate velit esse cillum dolore eu fugiat nulla pariatur. Excepteur sint occaecat cupidatat non proident, sunt in culpa qui officia deserunt mollit.</blockquote>
    <cite>Carla Benton, Manager</cite>
  </div>
  <div class="avatar" style="left:491px;top:236px" role="img" aria-label="Portrait photo of the reviewer"></div>

  <div class="avatar" style="left:634px;top:236px" role="img" aria-label="Portrait photo of the reviewer"></div>
  <div class="quote quote-right" style="top:236px">
    <blockquote>At vero eos et accusamus et iusto odio dignissimos ducimus qui blanditiis praesentium voluptatum deleniti atque corrupti quos dolores et quas molestias excepturi sint occaecati asperiores.</blockquote>
    <cite>Owen Pratley, Developer</cite>
  </div>
</section>

<section class="likes">
  <div class="likes-rule"></div>
  <div class="likes-pill">
    <svg class="likes-thumb" width="20" height="20" viewBox="0 0 20 20"><path d="M3 9h3v9H3zM7 9l4-7c1.5 0 2 1 1.6 2.6L12 8h5c1 0 1.6.9 1.4 1.8l-1.5 6.4c-.2.8-.9 1.3-1.7 1.3H7z" fill="#ccc"/></svg>
    <span class="likes-btn">Like</span>
    <span class="likes-count">You and 4k others like this.</span>
  </div>
</section>

<footer class="footer">
  <div class="footer-nav">
    <svg width="14" height="14" viewBox="0 0 14 14"><circle cx="5.5" cy="5.5" r="4" fill="none" stroke="#333" stroke-width="2"/><path d="M8.5 8.5 13 13" stroke="#333" stroke-width="2"/></svg>
    <span>Help &amp; Contact</span><span>Support</span><span>Project</span><span>Clients</span>
  </div>
  <div class="footer-brand">
    <div class="brand-name"><span class="brand-mark"></span>KELVANBROOK</div>
    <div class="brand-tag">www.kelvanbrook.com</div>
  </div>
  <div class="footer-rule"></div>
  <div class="footer-links">
    <span>About</span><span>Blog</span><span>Careers</span><span>Public Policy</span><span>Sitemap</span><span>Partners</span>
  </div>
  <div class="footer-social"><span></span><span></span><span></span></div>
  <div class="footer-legal"><span>© 2007–2017</span><span>Privacy</span><span>Legal</span></div>
  <div class="footer-base"></div>
</footer>

</body>
</html>
```